Business card for medical clinic

I need an upmarket, modern medical/health business card for my clinic

Contact Information for Business Card

name, address, email, qr code

```html
<!DOCTYPE html>
<html lang="en">
<head>
<meta charset="utf-8">
<title>Meridian Care Partners – Business Card</title>
<link href="https://fonts.googleapis.com/css2?family=Montserrat:wght@400;500;700&display=swap" rel="stylesheet">
<style>
  :root {
    --bg: #9a9a9a;
    --paper: #ffffff;
    --navy: #1f2b47;
    --steel: #2d5a78;
    --sky: #29a8dc;
    --accent: #2f8fc2;
    --ink: #1c1c1c;
  }
  * { margin: 0; padding: 0; box-sizing: border-box; }
  html, body { width: 1093px; height: 1200px; overflow: hidden; }
  body {
    background: var(--bg);
    font-family: "Montserrat", sans-serif;
    position: relative;
  }
  .card { position: absolute; }

  .card-front {
    left: 264px; top: 225px; width: 581px; height: 363px;
    background: var(--paper);
  }
  .front-band {
    position: absolute; left: 0; bottom: 0; width: 100%; height: 15px;
    background: linear-gradient(90deg, var(--navy) 0%, var(--steel) 45%, var(--accent) 100%);
  }
  .brand {
    position: absolute;
    display: flex; align-items: center; gap: 10px;
    font-weight: 700; letter-spacing: 0.04em; white-space: nowrap;
  }
  .brand-name { line-height: 1.15; }
  .brand-dot { border-radius: 50%; flex: none; }
  .front-brand {
    left: 80px; top: 201px; transform: translateY(-50%);
    font-size: 15px; color: var(--steel);
  }
  .front-brand .brand-dot { width: 28px; height: 28px; background: var(--accent); }

  .divider {
    position: absolute; left: 291px; top: 110px; width: 1px; height: 172px;
    background: var(--accent);
  }
  .details { position: absolute; left: 305px; top: 108px; }
  .person-name {
    font-size: 21px; font-weight: 700; line-height: 1;
    background: linear-gradient(90deg, var(--accent), var(--steel));
    -webkit-background-clip: text; background-clip: text; color: transparent;
  }
  .person-role { font-size: 12.5px; color: var(--ink); margin-top: 8px; }
  .contact-list { list-style: none; margin-top: 20px; }
  .contact-list li {
    display: flex; align-items: center; gap: 8px;
    font-size: 12.5px; color: var(--ink); height: 25px;
  }
  .contact-list svg { width: 13px; height: 13px; flex: none; }
  .address { font-size: 13.5px; color: var(--ink); line-height: 1.2; margin-top: 16px; }

  .card-back {
    left: 264px; top: 615px; width: 595px; height: 367px;
    background: linear-gradient(150deg, var(--navy) 0%, var(--steel) 45%, #2f86b2 75%, var(--sky) 100%);
  }
  .back-brand {
    left: 50%; top: 50%; transform: translate(-50%, -50%);
    font-size: 26px; color: var(--paper); gap: 16px;
  }
  .back-brand .brand-dot { width: 52px; height: 52px; border: 3px solid var(--paper); }
</style>
</head>
<body>
  <section class="card card-front">
    <div class="brand front-brand"><span class="brand-dot"></span><span class="brand-name">MERIDIAN CARE<br>PARTNERS</span></div>
    <div class="divider"></div>
    <div class="details">
      <h1 class="person-name">Daniel Brooks</h1>
      <p class="person-role">Managing Director</p>
      <ul class="contact-list">
        <li>
          <svg viewBox="0 0 24 24" aria-hidden="true"><path fill="#2f8fc2" d="M6.6 10.8a15.1 15.1 0 0 0 6.6 6.6l2.2-2.2c.3-.3.7-.4 1-.2 1.1.4 2.3.6 3.6.6.6 0 1 .4 1 1V20c0 .6-.4 1-1 1A17 17 0 0 1 3 4c0-.6.4-1 1-1h3.5c.6 0 1 .4 1 1 0 1.3.2 2.5.6 3.6.1.3 0 .7-.2 1z"/></svg>
          555.214.7730
        </li>
        <li>
          <svg viewBox="0 0 24 24" aria-hidden="true"><rect x="2" y="5" width="20" height="14" rx="1.5" fill="#29a8dc"/><path d="M2 6l10 7 10-7" fill="none" stroke="#fff" stroke-width="1.6"/></svg>
          info@meridiancare.com
        </li>
        <li>
          <svg viewBox="0 0 24 24" aria-hidden="true"><circle cx="12" cy="12" r="10" fill="#29a8dc"/><path d="M2 12h20M12 2c3 3 3 17 0 20M12 2c-3 3-3 17 0 20" fill="none" stroke="#fff" stroke-width="1.3"/></svg>
          www.meridiancare.com
        </li>
      </ul>
      <p class="address">248 Cedar Hollow Lane<br>Brandon, MS 39042</p>
    </div>
    <div class="front-band"></div>
  </section>

  <section class="card card-back">
    <div class="brand back-brand"><span class="brand-dot"></span><span class="brand-name">MERIDIAN CARE<br>PARTNERS</span></div>
  </section>
</body>
</html>
```